BVM Marketing Postcard

Design a 2 Sided marketing postcard for our Real estate management caompany. Looking for a professional yet fresh look that will be printed on a 6"x9" glossy flier

Contact information is www.brixleymanagement.example brixleymanagement@postwellmail.example and 555-014-7283

WE are targeting small condo and town home properties to take on their administrative responsibilities of management

```html
<!DOCTYPE html>
<html lang="en">
<head>
<meta charset="utf-8">
<title>BVM Marketing Postcard</title>
<link rel="stylesheet" href="https://fonts.googleapis.com/css2?family=Montserrat:wght@400;500;600;700&display=swap">
<style>
:root{
  --ink:#2a2118;
  --gold:#f4b41a;
  --paper:#ffffff;
  --stripe:#ececec;
  --band:#8c8c8c;
  --text:#222;
  --rule:#c9c9c9;
  --stage:#e9e6e1;
}
*{box-sizing:border-box;margin:0;padding:0}
html,body{width:1200px;height:903px;overflow:hidden;background:var(--stage);font-family:"Montserrat",sans-serif;color:var(--text)}
.canvas{position:relative;width:1200px;height:903px}
.card{position:absolute;width:570px;height:380px;background:var(--paper);box-shadow:0 6px 18px rgba(0,0,0,.18);overflow:hidden}
.card--front{left:20px;top:80px;padding:10px}
.card--back{left:610px;top:440px}

/* front */
.front{position:relative;width:100%;height:100%;border:1px solid var(--ink);display:flex;flex-direction:column}
.front__head{background:var(--ink);color:#fff;padding:12px 16px 10px;text-align:center}
.title{color:var(--gold);font-weight:700;font-size:20px;line-height:1.1}
.tagline{font-size:9px;margin-top:4px}
.front__body{flex:1;display:flex}
.col{flex:1;display:flex;flex-direction:column}
.col+.col{border-left:2px solid var(--band)}
.col__head{background:var(--band);color:#fff;font-weight:700;font-size:10.5px;padding:4px 10px}
.subhead{font-weight:700;font-size:11px;padding:4px 10px 2px}
.list{list-style:none}
.list li{display:flex;gap:5px;font-size:7.6px;line-height:1.25;padding:2.5px 10px}
.list li:nth-child(even){background:var(--stripe)}
.tick{flex:0 0 8px;height:8px;margin-top:1px}
.front__foot{background:var(--ink);color:#fff;display:flex;justify-content:space-around;align-items:center;height:28px;font-size:9.5px;font-weight:500}
.contact{display:flex;align-items:center;gap:5px}
.icon{width:10px;height:10px}

/* back */
.back__left{position:absolute;left:0;top:0;width:310px;height:380px;display:flex;flex-direction:column}
.back__head{background:var(--ink);padding:22px 18px 12px;height:82px}
.back__head .title{font-size:18px;text-align:left}
.back__body{flex:1;padding:8px 14px 4px}
.back__body .list li{font-size:8px;padding:3px 0;background:none}
.back__foot{background:var(--ink);color:#fff;padding:10px 18px;height:92px}
.back__foot .label{color:var(--gold);font-weight:700;font-size:10px;letter-spacing:.5px;margin-bottom:6px}
.back__foot .contact{font-size:9px;margin-bottom:4px}
.divider{position:absolute;left:310px;top:0;width:6px;height:380px;background:var(--band)}
.back__right{position:absolute;left:316px;top:0;right:0;height:380px}
.stamp{position:absolute;right:22px;top:22px;width:56px;height:64px;background:#d9d9d9}
.address{position:absolute;left:36px;top:110px;font-size:11px;line-height:1.35}
.line{position:absolute;left:36px;right:26px;height:1px;background:var(--rule)}
.gold-strip{position:absolute;left:0;right:0;bottom:0;height:8px;background:var(--gold)}
</style>
</head>
<body>
<div class="canvas">

  <section class="card card--front" aria-label="Postcard front">
    <div class="front">
      <header class="front__head">
        <h1 class="title">Brixley Property Management LLC (BVM)</h1>
        <p class="tagline">Improve compliance, reporting, and communication amongst all owners and board members</p>
      </header>
      <div class="front__body">
        <div class="col">
          <div class="col__head">Who we are:</div>
          <ul class="list">
            <li><svg class="tick" viewBox="0 0 10 10"><circle cx="5" cy="5" r="4.2" fill="none" stroke="#222"/><path d="M3 5.2l1.4 1.4L7 3.8" fill="none" stroke="#222"/></svg>A professional services organization with a focus on small (3-10 unit) residential buildings</li>
            <li><svg class="tick" viewBox="0 0 10 10"><circle cx="5" cy="5" r="4.2" fill="none" stroke="#222"/><path d="M3 5.2l1.4 1.4L7 3.8" fill="none" stroke="#222"/></svg>Over 30 years of combined experience in real estate &amp; property management</li>
            <li><svg class="tick" viewBox="0 0 10 10"><circle cx="5" cy="5" r="4.2" fill="none" stroke="#222"/><path d="M3 5.2l1.4 1.4L7 3.8" fill="none" stroke="#222"/></svg>Professional, courteous, timely service that is technologically driven</li>
          </ul>
          <h2 class="subhead">Why use BVM?</h2>
          <ul class="list">
            <li><svg class="tick" viewBox="0 0 10 10"><circle cx="5" cy="5" r="4.2" fill="none" stroke="#222"/><path d="M3 5.2l1.4 1.4L7 3.8" fill="none" stroke="#222"/></svg>Owners are rarely suited to manage associations &amp; the burden often falls unfairly on one or two individuals to do all the work</li>
            <li><svg class="tick" viewBox="0 0 10 10"><circle cx="5" cy="5" r="4.2" fill="none" stroke="#222"/><path d="M3 5.2l1.4 1.4L7 3.8" fill="none" stroke="#222"/></svg>Low monthly fees tailored to your needs</li>
            <li><svg class="tick" viewBox="0 0 10 10"><circle cx="5" cy="5" r="4.2" fill="none" stroke="#222"/><path d="M3 5.2l1.4 1.4L7 3.8" fill="none" stroke="#222"/></svg>The association's board of directors maintains control of all decision making</li>
          </ul>
        </div>
        <div class="col">
          <div class="col__head">What we do:</div>
          <ul class="list">
            <li><svg class="tick" viewBox="0 0 10 10"><circle cx="5" cy="5" r="4.2" fill="none" stroke="#222"/><path d="M3 5.2l1.4 1.4L7 3.8" fill="none" stroke="#222"/></svg>Remove the administrative burden of managing small residential buildings</li>
            <li><svg class="tick" viewBox="0 0 10 10"><circle cx="5" cy="5" r="4.2" fill="none" stroke="#222"/><path d="M3 5.2l1.4 1.4L7 3.8" fill="none" stroke="#222"/></svg>Utilize economies of scale to reduce expenses for all owners across a wide variety of service providers</li>
            <li><svg class="tick" viewBox="0 0 10 10"><circle cx="5" cy="5" r="4.2" fill="none" stroke="#222"/><path d="M3 5.2l1.4 1.4L7 3.8" fill="none" stroke="#222"/></svg>Collect all assessments and pay all bills</li>
            <li><svg class="tick" viewBox="0 0 10 10"><circle cx="5" cy="5" r="4.2" fill="none" stroke="#222"/><path d="M3 5.2l1.4 1.4L7 3.8" fill="none" stroke="#222"/></svg>Provide monthly accounting reconciliation and reporting</li>
            <li><svg class="tick" viewBox="0 0 10 10"><circle cx="5" cy="5" r="4.2" fill="none" stroke="#222"/><path d="M3 5.2l1.4 1.4L7 3.8" fill="none" stroke="#222"/></svg>Provide access to BVM's client portal with a central repository of all association materials (bylaws, financials, meeting minutes, communications, etc)</li>
            <li><svg class="tick" viewBox="0 0 10 10"><circle cx="5" cy="5" r="4.2" fill="none" stroke="#222"/><path d="M3 5.2l1.4 1.4L7 3.8" fill="none" stroke="#222"/></svg>Issue 1099s to all contractors as required by law</li>
            <li><svg class="tick" viewBox="0 0 10 10"><circle cx="5" cy="5" r="4.2" fill="none" stroke="#222"/><path d="M3 5.2l1.4 1.4L7 3.8" fill="none" stroke="#222"/></svg>Prepare year-end financial statements</li>
            <li><svg class="tick" viewBox="0 0 10 10"><circle cx="5" cy="5" r="4.2" fill="none" stroke="#222"/><path d="M3 5.2l1.4 1.4L7 3.8" fill="none" stroke="#222"/></svg>Lender &amp; legal HOA documents for mortgage companies and sales</li>
          </ul>
        </div>
      </div>
      <footer class="front__foot">
        <span class="contact"><svg class="icon" viewBox="0 0 10 10"><path d="M2 1l2 .5.5 2-1 1a6 6 0 0 0 2 2l1-1 2 .5.5 2c-4 1-9-4-8-8z" fill="#f4b41a"/></svg>555-014-7283</span>
        <span class="contact"><svg class="icon" viewBox="0 0 10 10"><rect x="1" y="2" width="8" height="6" fill="#f4b41a"/><path d="M1 2l4 3 4-3" fill="none" stroke="#2a2118"/></svg>brixleymanagement@postwellmail.example</span>
        <span class="contact"><svg class="icon" viewBox="0 0 10 10"><circle cx="5" cy="5" r="4" fill="#f4b41a"/><path d="M1 5h8M5 1c-2 2.5-2 5.5 0 8M5 1c2 2.5 2 5.5 0 8" fill="none" stroke="#2a2118" stroke-width=".6"/></svg>www.brixleymanagement.example</span>
      </footer>
    </div>
  </section>

  <section class="card card--back" aria-label="Postcard back">
    <div class="back__left">
      <header class="back__head">
        <h2 class="title">Brixley Property Management LLC (BVM)</h2>
      </header>
      <div class="back__body">
        <ul class="list">
          <li><svg class="tick" viewBox="0 0 10 10"><circle cx="5" cy="5" r="4.2" fill="none" stroke="#222"/><path d="M3 5.2l1.4 1.4L7 3.8" fill="none" stroke="#222"/></svg>Cost effective property management solution for 3-10 unit buildings</li>
          <li><svg class="tick" viewBox="0 0 10 10"><circle cx="5" cy="5" r="4.2" fill="none" stroke="#222"/><path d="M3 5.2l1.4 1.4L7 3.8" fill="none" stroke="#222"/></svg>Prices starting as low as $100/month</li>
          <li><svg class="tick" viewBox="0 0 10 10"><circle cx="5" cy="5" r="4.2" fill="none" stroke="#222"/><path d="M3 5.2l1.4 1.4L7 3.8" fill="none" stroke="#222"/></svg>Utilize our economies of scale to reduce costs across existing services (trash, insurance, maintenance, etc)</li>
          <li><svg class="tick" viewBox="0 0 10 10"><circle cx="5" cy="5" r="4.2" fill="none" stroke="#222"/><path d="M3 5.2l1.4 1.4L7 3.8" fill="none" stroke="#222"/></svg>Eliminate the unfair burden placed on a few owners to do all the work while others free-ride</li>
          <li><svg class="tick" viewBox="0 0 10 10"><circle cx="5" cy="5" r="4.2" fill="none" stroke="#222"/><path d="M3 5.2l1.4 1.4L7 3.8" fill="none" stroke="#222"/></svg>Improve communication amongst all owners and board members</li>
          <li><svg class="tick" viewBox="0 0 10 10"><circle cx="5" cy="5" r="4.2" fill="none" stroke="#222"/><path d="M3 5.2l1.4 1.4L7 3.8" fill="none" stroke="#222"/></svg>The association's board of directors maintain all decision-making power</li>
          <li><svg class="tick" viewBox="0 0 10 10"><circle cx="5" cy="5" r="4.2" fill="none" stroke="#222"/><path d="M3 5.2l1.4 1.4L7 3.8" fill="none" stroke="#222"/></svg>Utilize our vetted service providers for prompt job completion and fair pricing</li>
        </ul>
      </div>
      <footer class="back__foot">
        <p class="label">CONTACT INFORMATION</p>
        <p class="contact"><svg class="icon" viewBox="0 0 10 10"><path d="M2 1l2 .5.5 2-1 1a6 6 0 0 0 2 2l1-1 2 .5.5 2c-4 1-9-4-8-8z" fill="#f4b41a"/></svg>555-014-7283</p>
        <p class="contact"><svg class="icon" viewBox="0 0 10 10"><rect x="1" y="2" width="8" height="6" fill="#f4b41a"/><path d="M1 2l4 3 4-3" fill="none" stroke="#2a2118"/></svg>brixleymanagement@postwellmail.example</p>
        <p class="contact"><svg class="icon" viewBox="0 0 10 10"><circle cx="5" cy="5" r="4" fill="#f4b41a"/><path d="M1 5h8M5 1c-2 2.5-2 5.5 0 8M5 1c2 2.5 2 5.5 0 8" fill="none" stroke="#2a2118" stroke-width=".6"/></svg>www.brixleymanagement.example</p>
      </footer>
    </div>
    <div class="divider"></div>
    <div class="back__right">
      <div class="stamp"></div>
      <p class="address">48 Larkspur Court<br>Fernhollow, IL 60000</p>
      <div class="line" style="top:190px"></div>
      <div class="line" style="top:225px"></div>
      <div class="line" style="top:260px"></div>
      <div class="gold-strip"></div>
    </div>
  </section>

</div>
</body>
</html>
```